Korvile

I'd like new business card design options. I'll need to provide updated contact info although after the deign is complete. We are in IT, specifically in the data backup, archiving and disaster recovery verticals.

Industry/Entity Type

Business

```html
<!DOCTYPE html>
<html lang="en">
<head>
<meta charset="utf-8">
<title>Korvile business cards</title>
<link rel="stylesheet" href="https://fonts.googleapis.com/css2?family=Roboto:wght@400;700&family=Roboto+Condensed:wght@400;700&display=swap">
<style>
  :root {
    --backdrop: #e9e6e1;
    --card-white: #f7f8f9;
    --brand-blue: #0b5cb8;
    --deep-blue: #0750a6;
    --sky-blue: #2a9be0;
    --text-grey: #3c3f44;
    --map-tint: #dbe8f1;
    --white: #ffffff;
  }
  * { box-sizing: border-box; margin: 0; padding: 0; }
  html, body { width: 1200px; height: 911px; overflow: hidden; }
  body { background: var(--backdrop); position: relative; font-family: "Roboto", sans-serif; }

  .card {
    position: absolute;
    width: 540px;
    height: 309px;
    border-radius: 18px;
    overflow: hidden;
    box-shadow: 0 12px 28px rgba(0,0,0,.22);
  }

  /* Front */
  .card-front { left: 70px; top: 100px; background: var(--card-white); }
  .map-area {
    position: absolute; right: 0; top: 0; width: 330px; height: 200px;
    background: radial-gradient(ellipse at 60% 45%, var(--map-tint) 0%, rgba(219,232,241,.5) 55%, rgba(247,248,249,0) 80%);
  }
  .contact-strip {
    position: absolute; left: 0; top: 0; bottom: 0; width: 62px;
    background: linear-gradient(to bottom, var(--sky-blue) 0 34%, var(--deep-blue) 34% 100%);
  }
  .strip-dot {
    position: absolute; left: 12px; top: 52px; width: 54px; height: 54px;
    border-radius: 50%; background: var(--white);
  }
  .strip-icon { position: absolute; left: 21px; width: 20px; height: 20px; }
  .icon-person { top: 146px; }
  .icon-pin { top: 196px; }
  .icon-phone { top: 240px; }
  .front-text { position: absolute; left: 96px; top: 30px; }
  .brand-name {
    font-family: "Roboto", sans-serif; font-weight: 700; font-size: 38px;
    letter-spacing: 5px; color: var(--brand-blue); line-height: 1;
  }
  .tagline {
    font-family: "Roboto", sans-serif; font-weight: 700; font-size: 13px;
    letter-spacing: 3px; color: var(--sky-blue); margin-top: 4px;
  }
  .person-name {
    font-family: "Roboto Condensed", sans-serif; font-weight: 700; font-size: 19px;
    color: var(--brand-blue); margin-top: 22px; text-transform: uppercase;
  }
  .person-role, .person-email {
    font-family: "Roboto Condensed", sans-serif; font-size: 15px; color: var(--sky-blue); line-height: 1.25;
  }
  .person-role { text-transform: uppercase; }
  .details {
    font-family: "Roboto Condensed", sans-serif; font-size: 14px; color: var(--text-grey);
    line-height: 1.3; margin-top: 10px;
  }
  .details + .details { margin-top: 6px; }

  /* Back */
  .card-back { left: 590px; top: 500px; background: var(--brand-blue); color: var(--white); }
  .back-brand { position: absolute; left: 150px; top: 58px; display: flex; align-items: center; gap: 16px; }
  .back-dot { width: 52px; height: 52px; border-radius: 50%; background: var(--white); }
  .back-brand .brand-name { color: var(--white); font-size: 44px; letter-spacing: 8px; }
  .back-tagline { position: absolute; left: 218px; top: 112px; font-weight: 700; font-size: 14px; letter-spacing: 4px; }
  .services { position: absolute; left: 40px; top: 180px; font-family: "Roboto Condensed", sans-serif; }
  .services-label { font-size: 13px; text-transform: uppercase; letter-spacing: 1px; opacity: .9; }
  .services-products { font-weight: 700; font-size: 19px; margin-top: 4px; }
  .services-products sup { font-size: 9px; font-weight: 400; }
  .services-list { font-size: 14px; margin-top: 6px; opacity: .95; }
</style>
</head>
<body>

<section class="card card-front" aria-label="Business card front">
  <div class="map-area" role="img" aria-label="Faint world map background"></div>
  <div class="contact-strip">
    <svg class="strip-icon icon-person" viewBox="0 0 20 20" aria-hidden="true"><circle cx="10" cy="6" r="4" fill="#fff"/><path d="M2 19c0-5 3.5-7 8-7s8 2 8 7z" fill="#fff"/></svg>
    <svg class="strip-icon icon-pin" viewBox="0 0 20 20" aria-hidden="true"><path d="M10 1a6 6 0 0 0-6 6c0 5 6 12 6 12s6-7 6-12a6 6 0 0 0-6-6z" fill="#fff"/><circle cx="10" cy="7" r="2.3" fill="#0750a6"/></svg>
    <svg class="strip-icon icon-phone" viewBox="0 0 20 20" aria-hidden="true"><path d="M5 2l3 3-2 2.5a11 11 0 0 0 6.5 6.5L15 12l3 3-2.5 3C8 17 3 12 2 4.5z" fill="#fff"/></svg>
  </div>
  <div class="strip-dot" aria-hidden="true"></div>

  <div class="front-text">
    <div class="brand-name">KORVILE</div>
    <div class="tagline">Backup You Can Trust</div>
    <div class="person-name">Daniel R. Hollis, Ph.D.</div>
    <div class="person-role">President, CTO</div>
    <div class="person-email">daniel.hollis@korvile.com</div>
    <div class="details">402 North Alder Street<br>Brenford, Texas 75091</div>
    <div class="details">800.555.0147<br>928.555.0182<br>www.korvile.com</div>
  </div>
</section>

<section class="card card-back" aria-label="Business card back">
  <div class="back-brand">
    <div class="back-dot" aria-hidden="true"></div>
    <div class="brand-name">KORVILE</div>
  </div>
  <div class="back-tagline">Backup You Can Trust</div>
  <div class="services">
    <div class="services-label">Providers of</div>
    <div class="services-products">VaultKeep<sup>TM</sup> and RackKeep<sup>TM</sup></div>
    <div class="services-list">Online PC backup | Continuous Server Backup | Data Archiving</div>
  </div>
</section>

</body>
</html>
```